Marlow Estate Fixers (Handyman / Home Improvement Company)

Looking for a double sided professional looking business card with Logo attached to be highlighted on one side and throwing in an image of a handyman as an option would be nice to see as well. We are a company focused on providing quality Handyman and Home improvement services in a timely manner that is done right the first time with integrity

Industry/Entity Type

Handyman / Home Improvement

Contact Information for Business Card

(LOGO, Name, Mobile and office phone numbers, email) on front side of card, (the words "The SOLUTION to all of your Handyman and Home Improvement needs" followed by "Family Owned and Operated" at the very bottom) on the back.

Colors
EB3D1F
EC4F4E
F09395
F8D3D4
FCEDEE

Requirements
Must have
• Red, Gray, Black Color scheme
Should not have
• No Yellow or Blue colors

```html
<!DOCTYPE html>
<html lang="en">
<head>
<meta charset="UTF-8">
<title>Marlow Estate Fixers – Business Card</title>
<link rel="stylesheet" href="https://fonts.googleapis.com/css2?family=Montserrat:wght@400;500;700&family=Oswald:wght@500;700&display=swap">
<style>
  :root {
    --brand-red: #e8292e;
    --deep-red: #c81f24;
    --ink: #1b1b1b;
    --gray: #3a3a3a;
    --paper: #ffffff;
    --backdrop: #1d1d1d;
    --figure-a: #c8323a;
    --figure-b: #5a4a6a;
  }
  * { margin: 0; padding: 0; box-sizing: border-box; }
  html, body {
    width: 1200px; height: 1059px; overflow: hidden;
    background: var(--backdrop);
    font-family: "Montserrat", sans-serif;
  }
  .canvas { position: relative; width: 1200px; height: 1059px; }

  .card {
    position: absolute; border-radius: 22px; overflow: hidden;
  }
  .card--front { left: 260px; top: 95px; width: 715px; height: 408px; background: var(--paper); }
  .card--back  { left: 262px; top: 529px; width: 716px; height: 410px; background: var(--brand-red); }

  /* front */
  .brand-mark {
    position: absolute; display: flex; align-items: center; gap: 10px;
  }
  .brand-mark__square { width: 22px; height: 22px; flex: none; }
  .brand-mark__name { font-weight: 700; line-height: 1.1; }

  .card--front .brand-mark { left: 99px; top: 152px; width: 230px; }
  .card--front .brand-mark__square { background: var(--brand-red); }
  .card--front .brand-mark__name { color: var(--ink); font-size: 27px; }

  .divider {
    position: absolute; left: 352px; top: 120px; width: 2px; height: 170px;
    background: linear-gradient(to bottom, transparent, var(--brand-red) 15%, var(--brand-red) 85%, transparent);
  }
  .person { position: absolute; left: 383px; top: 118px; }
  .person__name { color: var(--brand-red); font-weight: 700; font-size: 27px; letter-spacing: 0.2px; }
  .person__role { color: var(--ink); font-size: 18px; font-weight: 400; margin-top: 4px; }

  .contacts { position: absolute; left: 383px; top: 196px; list-style: none; }
  .contacts__item { display: flex; align-items: center; height: 31px; color: var(--ink); font-size: 19px; }
  .contacts__icon { width: 20px; height: 20px; margin-right: 12px; flex: none; }

  /* back */
  .figure-area {
    position: absolute; left: 23px; top: 21px; width: 297px; height: 382px;
    border-radius: 150px 150px 30px 30px;
    background: linear-gradient(170deg, var(--figure-a) 0%, var(--figure-b) 60%, var(--deep-red) 100%);
    opacity: 0.55;
  }
  .tagline {
    position: absolute; left: 346px; top: 12px; width: 304px;
    font-family: "Oswald", sans-serif; font-weight: 500; color: var(--paper);
    text-align: center; font-size: 28px; line-height: 40px;
  }
  .tagline strong { font-weight: 700; font-size: 31px; }

  .card--back .brand-mark { left: 395px; top: 212px; width: 230px; justify-content: center; }
  .card--back .brand-mark__square { background: var(--paper); }
  .card--back .brand-mark__name { color: var(--paper); font-size: 27px; }

  .footer-line {
    position: absolute; left: 346px; top: 370px; width: 304px; text-align: center;
    color: var(--paper); font-weight: 700; font-size: 17px;
  }
</style>
</head>
<body>
<main class="canvas">

  <section class="card card--front">
    <div class="brand-mark">
      <span class="brand-mark__square"></span>
      <span class="brand-mark__name">Marlow Estate Fixers</span>
    </div>
    <div class="divider"></div>
    <div class="person">
      <h1 class="person__name">Daniel Hartley</h1>
      <p class="person__role">Owner</p>
    </div>
    <ul class="contacts">
      <li class="contacts__item">
        <svg class="contacts__icon" viewBox="0 0 20 20"><rect x="5" y="1" width="10" height="18" rx="2" fill="none" stroke="#e8292e" stroke-width="2"/><circle cx="10" cy="15.5" r="1.2" fill="#e8292e"/></svg>
        044-555 018 240
      </li>
      <li class="contacts__item">
        <svg class="contacts__icon" viewBox="0 0 20 20"><path d="M1 7c0-3 4-4 9-4s9 1 9 4l-4 1-1-2H6L5 8z" fill="#e8292e"/><path d="M5 9h10l3 8H2z" fill="#e8292e"/><circle cx="10" cy="13" r="2" fill="#fff"/></svg>
        044-555 018 240
      </li>
      <li class="contacts__item">
        <svg class="contacts__icon" viewBox="0 0 20 20"><rect x="1" y="4" width="18" height="13" fill="#e8292e"/><path d="M1 4l9 7 9-7" fill="none" stroke="#fff" stroke-width="1.6"/></svg>
        info@marlowfixers.com
      </li>
    </ul>
  </section>

  <section class="card card--back">
    <div class="figure-area" role="img" aria-label="Illustration of a smiling handyman in work overalls holding a pipe wrench and spanner"></div>
    <p class="tagline">Your <strong>SOLUTION</strong> to all of your <strong>Handyman</strong> and <strong>Home Improvement</strong> Needs</p>
    <div class="brand-mark">
      <span class="brand-mark__square"></span>
      <span class="brand-mark__name">Marlow Estate Fixers</span>
    </div>
    <p class="footer-line">Family Owned and Operated</p>
  </section>

</main>
</body>
</html>
```